Luxury sell sheet flyer Design

We need two luxury/premium looking sales flyer - one for luxury and one for travel-

Please find flyers from last year (2015) attached. Please copy the pictures and the look and feel (and colors), and use the content form the 2016 documents.

These flyers will be used for corporate subscription sales and targetted at CMOs and Marketing heads. As such they should convey a very premium look and feel.

Please provide in format that we can make text edits in later.

USA, UK, Asia

Travel

Serif

• Good copyright free pictures, no clip art, that show a very premium look and feel for a corporate flyer
• clean feel, not cluttered
• clip art

```html
<!DOCTYPE html>
<html lang="en">
<head>
<meta charset="utf-8">
<title>Affluent Asian Travel Consumer Reports</title>
<link rel="stylesheet" href="https://fonts.googleapis.com/css2?family=Tinos:ital,wght@0,400;0,700;1,400;1,700&family=Roboto+Condensed:wght@700&family=Montserrat:wght@600&display=swap">
<style>
:root{
  --ink:#111;
  --rule:#9a9a9a;
  --brand:#8a2f8f;
  --band:#6b3a8c;
  --glow-lilac:#dcd3f4;
  --glow-pink:#f6dcef;
  --glow-blue:#d7e2f8;
  --badge:#d9d9de;
}
*{margin:0;padding:0;box-sizing:border-box}
html,body{width:927px;height:1200px;overflow:hidden}
body{
  position:relative;
  font-family:"Tinos","Times New Roman",serif;
  color:var(--ink);
  background:
    radial-gradient(ellipse 380px 300px at 860px 140px,var(--glow-blue),transparent 70%),
    radial-gradient(ellipse 420px 320px at 80px 380px,var(--glow-pink),transparent 70%),
    radial-gradient(ellipse 420px 360px at 900px 620px,var(--glow-lilac),transparent 70%),
    radial-gradient(ellipse 380px 300px at 120px 1080px,var(--glow-lilac),transparent 70%),
    #fbfbfe;
}
.abs{position:absolute}
.title{left:40px;top:20px;font-size:21px;font-weight:700;letter-spacing:.2px}
.lead{left:40px;top:49px;font-size:15px}
.cat-label{left:40px;top:80px;font-size:15px;font-weight:700;font-style:italic;text-decoration:underline}
.cat-table{left:40px;top:99px;width:758px;border-collapse:collapse;font-size:15px;background:#fff}
.cat-table td{border:1px solid var(--rule);height:26px;padding:0 0 0 18px;white-space:nowrap}
.intro{left:40px;top:190px;width:478px;font-size:15px;line-height:19px}
.intro p+p{margin-top:16px}
.intro .markets{font-weight:700}
.def-label{left:546px;top:193px;font-size:15px}
.def-table{left:542px;top:218px;width:260px;border-collapse:collapse;font-size:12.5px;background:#fff}
.def-table th,.def-table td{border:1px solid var(--rule);height:25.7px;padding:0 0 0 13px;text-align:left}
.def-table th{border:none;border-bottom:1px solid var(--rule);font-weight:700;font-size:12px}
.def-table td:first-child{font-weight:700;width:125px}
.divider{left:40px;top:470px;width:816px;height:1px;background:var(--rule)}
.col{font-size:12px;line-height:16.3px}
.col-left{left:40px;top:489px;width:382px}
.col-right{left:441px;top:489px;width:420px}
.col h3{font-size:12px;font-weight:700;display:inline}
.col p{margin-bottom:7px}
.col .kicker{font-weight:700}
.topics{display:flex;margin-top:0}
.topics ul{list-style:none}
.topics li{padding-left:10px;position:relative}
.topics li::before{content:"•";position:absolute;left:0}
.topics .sub li{padding-left:14px}
.topics .sub li::before{content:none}
.topics .t1{width:150px}
.topics .t2{width:230px;margin-top:16px}
.topics .t2 li{padding-left:16px}
.tier{margin-top:6px}
.tier strong{display:block}
.tier span{display:block;padding-left:15px}
.media-head{left:470px;top:1049px;font-family:"Roboto Condensed",Arial,sans-serif;font-size:14px;font-weight:700}
.media-box{left:449px;top:1069px;width:407px;height:102px;background:#fff;box-shadow:0 0 6px rgba(0,0,0,.12)}
.brand{left:65px;top:1111px;display:flex;align-items:center;gap:8px;font-family:"Montserrat",Arial,sans-serif;font-weight:600;font-size:22px;color:var(--brand)}
.brand i{width:12px;height:12px;border-radius:50%;background:var(--brand)}
.web{left:238px;top:1115px;font-family:"Montserrat",Arial,sans-serif;font-size:16px}
.band{left:0;top:1183px;width:927px;height:17px;background:var(--band)}
</style>
</head>
<body>
<h1 class="abs title">AFFLUENT ASIAN TRAVEL CONSUMER REPORTS</h1>
<p class="abs lead">The 2016 subscription includes two reports per market, one released half-way and the other one at the end of the year.</p>
<p class="abs cat-label">The following travel and luxury product categories are covered in each market:</p>
<table class="abs cat-table">
  <tr><td>Hotels (49 brands)</td><td>Cruise Lines (21 brands)</td><td>Airlines (50 brands)</td></tr>
  <tr><td>Travel Destinations (44 destinations</td><td>Designer Clothing &amp; Accessories (83 brands)</td><td>Watches (82 brands)</td></tr>
  <tr><td>Jewellery (39 brands)</td><td>Skincare (52 brands)</td><td>Makeup (49 brands)</td></tr>
</table>

<div class="abs intro">
  <p>In each market we are focusing on affluent travel consumers (approximately top-20% of the population based on household income) who have travelled internationally in the past 12 months or planning to travel in the next 12 months. We are fielding two waves in 2016, and interviewing a total of n=300 affluent consumers in each market (at least 100 respondents in each market are past-12/next-12-month cruise travellers/intenders).</p>
  <p>Markets included in the study (content is partially trended to last year in all markets)<br><span class="markets">• China • India • Singapore &nbsp;• Hong Kong &nbsp;• Malaysia &nbsp;• S. Korea<br>• Taiwan &nbsp;• Japan</span></p>
  <p style="margin-top:10px">Other markets, such as, Indonesia, Thailand, and Australia can be added by request.</p>
</div>

<p class="abs def-label">Affluent consumer definitions are as follows:</p>
<table class="abs def-table">
  <tr><th>COUNTRY</th><th>Annual HHI</th></tr>
  <tr><td>China</td><td>CNY 200,000+</td></tr>
  <tr><td>India</td><td>INR 12,00,000+</td></tr>
  <tr><td>Singapore</td><td>SGD 110,000+</td></tr>
  <tr><td>Hong Kong</td><td>HKD 720,000+</td></tr>
  <tr><td>Malaysia</td><td>MYR 120,000+</td></tr>
  <tr><td>South Korea</td><td>KRW 78 million +</td></tr>
  <tr><td>Taiwan</td><td>NT$ 960,000+</td></tr>
  <tr><td>Japan</td><td>JPY 10,000,000+</td></tr>
</table>

<div class="abs divider"></div>

<section class="abs col col-left">
  <p class="kicker" style="margin-bottom:0">Key analytics in the reports include:</p>
  <p><strong>Luxury Brand Index –</strong> A tool to help brands understand how well they are meeting the expectation of their potential travel customers in relation to their competitors in different markets. The index is derived from the importance of different dimensions of luxury on category purchase intent and brands' ratings on the same dimensions.</p>
  <p><strong>Luxury Brand Media Reach –</strong> Gives the brands vital information on how well they are being noticed by travellers in the most relevant media touchpoints. This is calculated based on the importance of different media touchpoints for affecting category purchasing and recall of brand recall in the relevant touchpoints.</p>
  <p><strong>Luxury Consumer Segmentation</strong> - We have identified unique key luxury consumer types that are different in their motivations and purchase behaviour towards luxury brands. This segmentation will help brands understand their key consumer types in each market.</p>
  <p style="margin-bottom:0"><strong>Affluent Luxury Consumer Insights –</strong> We will have numerous analyses to help you understand and profile affluent Asian travel consumers in each market, looking at their purchase behaviour, media influences, psychographics, and demographics. Many of the analyses will be trended to understand shifts in consumer preferences. Key topics for the analyses include:</p>
  <div class="topics">
    <ul class="t1">
      <li>Purchase Triggers</li>
      <li>Most recent trip
        <ul class="sub">
          <li>Influences</li><li>Loyalty programs</li><li>Advertising</li><li>Recommendations</li><li>Editorials</li><li>Travel agents</li><li>How travel was booked</li><li>Class of travel</li><li>Destination type</li><li>Activities</li>
        </ul>
      </li>
    </ul>
    <ul class="t2">
      <li>What looking forward to from next trip?</li>
      <li>Travel and Luxury Categories and Brands Intended to Purchase</li>
      <li>Spend and Share of Wallet for Different Luxury Categories</li>
      <li>Media Touchpoints Relevant to Each Category</li>
      <li>Psychographics around Luxury Travel Purchase Behaviour</li>
      <li>Hobbies and Interests</li>
      <li>Travel preferences</li>
      <li>Affluent Travel Consumer Profiles</li>
    </ul>
  </div>
</section>

<section class="abs col col-right">
  <p><strong>SEMI-ANNUAL ROUNDTABLES</strong> (with Senior Executives from the Luxury Travel World)<br>These are private, invitation-only, informal lunch and evening sessions held quarterly at central premium locations in Hong Kong and Singapore. During these sessions we will share latest findings on affluent Asian travel consumers and moderate a discussion on topical themes among travel leaders (including executives from luxury travel brands and travel though leaders).</p>
  <p><strong>CUSTOM TABULATIONS OF DATA</strong><br>We will provide a set of tabulations of the data for all basic graphs included in the report with custom cuts (up to 20 banner points), e.g., you target consumer age groups, or consumers who are planning a purchase from your competitive brand set.</p>
  <p style="margin-top:12px;margin-bottom:0"><strong>SEMI-ANNUAL BRAINSTORMING SESSIONS</strong> (with Meridian Experts)<br>We will facilitate two brainstorming sessions (timed after the release of each of the Affluent Consumer and Luxury Brand Reports). In these two-hour sessions we walk you through the findings from the latest data release, and together with you look at implications the findings have on your specific brand(s), and brainstorm on how your brand can best make us of the findings. These sessions can be held in our or your premises in Singapore or Hong Kong.<br>2016 Premier Insights Travel Subscription Service has three optional service tiers:</p>
  <div class="tier"><strong>Premier Insights Plus</strong><span>2 Affluent Asian Travel Consumer Reports</span></div>
  <div class="tier" style="margin-top:0"><strong>Premier Insights Premium</strong><span>2 Affluent Asian Travel Consumer Reports</span><span>1 Invitation to Semi-annual Travel Leader Roundtables</span><span>1 Set of Custom Tabulations of Data (per market)</span></div>
  <div class="tier" style="margin-top:0"><strong>Premier Insights Prestige</strong><span>2 Affluent Asian Travel Consumer Reports</span><span>2 Invitations to Semi-annual Travel Leader Roundtables</span><span>2 Sets of Custom Tabulations of Data (per market)</span><span>2 Semi-annual Brainstorming Sessions (per market) or speaking engagements. (We have spoken at key events with GLTF, Prestige Ledger, Voyage Vision, GWT (Travel &amp; Luxury Summit), and Luxe Circle)</span></div>
</section>

<p class="abs media-head">Our research has been featured in international media, such as:</p>
<div class="abs media-box" role="img" aria-label="Row of media outlet badges">
  <svg width="407" height="102" viewBox="0 0 407 102">
    <g fill="var(--badge)">
      <rect x="10" y="10" width="48" height="12"/><rect x="66" y="10" width="64" height="12"/><rect x="136" y="9" width="34" height="14"/>
      <rect x="178" y="11" width="54" height="10"/><rect x="240" y="8" width="54" height="15"/><rect x="302" y="10" width="50" height="12"/>
      <rect x="10" y="43" width="52" height="11"/><rect x="70" y="43" width="60" height="11"/><rect x="136" y="40" width="56" height="15"/>
      <rect x="200" y="39" width="62" height="16"/><rect x="270" y="44" width="52" height="10"/><rect x="328" y="40" width="44" height="14"/>
      <rect x="90" y="75" width="72" height="16"/><rect x="170" y="74" width="52" height="18"/><rect x="230" y="74" width="60" height="18"/>
    </g>
  </svg>
</div>

<div class="abs brand"><i></i>OPULENTIA</div>
<p class="abs web">www.opulentia-insights.com</p>
<div class="abs band"></div>
</body>
</html>
```